Software allocation system needs a business card design

We need a business card designed for our software platform - www.tallivo.com.au

At the moment the logo and website is all black and white, we are happy for suggestions on implementing some colour throughout either the logo or business card.

Industry/Entity Type

Software

Font styles to use
Sans Serif

Colors

Designer to choose colors to be used in the design.

```html
<!DOCTYPE html>
<html lang="en">
<head>
<meta charset="utf-8">
<title>Tallivo – Business Card</title>
<link rel="stylesheet" href="https://fonts.googleapis.com/css2?family=Arimo:wght@400;700&display=swap">
<style>
  :root {
    --card-light: #ececec;
    --card-mid: #d9d9d9;
    --card-dark: #c4c4c4;
    --ink: #1c1c1c;
    --ink-soft: #4a4a4a;
    --ink-muted: #5a5a5a;
    --label: #ffffff;
    --accent: #2a8bc4;
    --blue-1: #1d6aa3;
    --blue-2: #2a7fb8;
    --blue-3: #3b91c6;
    --blue-4: #4a9ccd;
    --blue-5: #2f9bd0;
    --blue-6: #5aaad6;
    --blue-7: #77b6da;
    --blue-8: #8dc0dc;
    --grey-band-1: #8a8a8a;
    --grey-band-2: #a3a3a3;
    --grey-band-3: #b8b8b8;
  }
  html, body {
    margin: 0;
    padding: 0;
    width: 1200px;
    height: 685px;
    overflow: hidden;
    background: #ffffff;
  }
  .card {
    position: relative;
    width: 1200px;
    height: 685px;
    overflow: hidden;
    font-family: "Arimo", Arial, sans-serif;
    background: radial-gradient(ellipse 70% 75% at 50% 45%, var(--card-light) 0%, var(--card-mid) 70%, var(--card-dark) 100%);
  }
  .tile-field {
    position: absolute;
    inset: 37px 0 18px 0;
    display: flex;
  }
  .tile-field span { flex: 1; }
  .tile-field span:nth-child(odd) { background: rgba(255,255,255,0.06); }
  .tile-field span:nth-child(3n) { background: rgba(0,0,0,0.03); }

  .top-band, .bottom-band {
    position: absolute;
    left: 0;
    width: 100%;
    display: flex;
  }
  .top-band { top: 0; height: 37px; }
  .bottom-band { bottom: 0; height: 18px; }
  .top-band span, .bottom-band span { flex: 1; }
  .top-band span:nth-child(1) { background: var(--blue-1); }
  .top-band span:nth-child(2) { background: var(--blue-2); }
  .top-band span:nth-child(3) { background: var(--blue-3); }
  .top-band span:nth-child(4) { background: var(--blue-4); }
  .top-band span:nth-child(5) { background: var(--blue-5); }
  .top-band span:nth-child(6) { background: var(--blue-6); }
  .top-band span:nth-child(7) { background: var(--blue-7); }
  .top-band span:nth-child(8) { background: var(--blue-8); }
  .top-band span:nth-child(9) { background: var(--blue-7); }
  .bottom-band span:nth-child(odd) { background: var(--grey-band-1); }
  .bottom-band span:nth-child(even) { background: var(--grey-band-2); }
  .bottom-band span:nth-child(3n) { background: var(--grey-band-3); }

  .backdrop-word {
    position: absolute;
    left: 155px;
    top: 40px;
    margin: 0;
    font-size: 205px;
    font-weight: 700;
    letter-spacing: 2px;
    line-height: 1;
    color: rgba(255,255,255,0.38);
  }

  .brand {
    position: absolute;
    left: 0;
    top: 160px;
    width: 100%;
    display: flex;
    justify-content: center;
    align-items: center;
    gap: 22px;
  }
  .brand-dot {
    width: 34px;
    height: 34px;
    border-radius: 50%;
    background: var(--accent);
  }
  .brand-name {
    margin: 0;
    font-size: 118px;
    font-weight: 400;
    letter-spacing: 10px;
    line-height: 1;
    color: var(--ink);
  }

  .tagline {
    position: absolute;
    left: 0;
    top: 296px;
    width: 100%;
    margin: 0;
    text-align: center;
    font-size: 32px;
    font-weight: 400;
    line-height: 1;
    color: var(--ink-soft);
  }
  .tagline-shade {
    position: absolute;
    left: 170px;
    top: 334px;
    width: 860px;
    height: 16px;
    background: radial-gradient(ellipse 50% 100% at 50% 0%, rgba(0,0,0,0.14), rgba(0,0,0,0));
  }

  .person {
    position: absolute;
    left: 0;
    top: 396px;
    width: 100%;
    text-align: center;
  }
  .person-name, .person-role {
    margin: 0;
    font-size: 34px;
    font-weight: 400;
    line-height: 50px;
  }
  .person-name { color: var(--ink-muted); }
  .person-role { color: var(--label); }

  .details {
    position: absolute;
    top: 551px;
    display: grid;
    grid-template-columns: auto auto;
    column-gap: 24px;
    font-size: 22px;
    line-height: 31px;
    margin: 0;
  }
  .details dt {
    font-weight: 700;
    color: var(--label);
    text-align: right;
  }
  .details dd {
    margin: 0;
    color: var(--ink-soft);
  }
  .details-address { left: 90px; }
  .details-contact { left: 713px; }
</style>
</head>
<body>
  <main class="card">
    <div class="tile-field" aria-hidden="true">
      <span></span><span></span><span></span><span></span><span></span><span></span><span></span><span></span><span></span>
    </div>
    <div class="top-band" aria-hidden="true">
      <span></span><span></span><span></span><span></span><span></span><span></span><span></span><span></span><span></span>
    </div>

    <p class="backdrop-word" aria-hidden="true">Tallivo</p>

    <div class="brand">
      <span class="brand-dot" aria-hidden="true"></span>
      <h1 class="brand-name">TALLIVO</h1>
    </div>

    <p class="tagline">PLANNING &amp; COMPLIANCE FOR HEAVY INDUSTRY</p>
    <div class="tagline-shade" aria-hidden="true"></div>

    <div class="person">
      <p class="person-name">John Doe</p>
      <p class="person-role">Managing Director</p>
    </div>

    <dl class="details details-address">
      <dt>address</dt>
      <dd>PO Box 512<br>Harbour Vale NSW 2188<br>Australia</dd>
    </dl>

    <dl class="details details-contact">
      <dt>telephone</dt><dd>01.23.45.67.89</dd>
      <dt>website</dt><dd>www.tallivo.com.au</dd>
      <dt>email</dt><dd>john@tallivo.com.au</dd>
    </dl>

    <div class="bottom-band" aria-hidden="true">
      <span></span><span></span><span></span><span></span><span></span><span></span><span></span><span></span><span></span>
    </div>
  </main>
</body>
</html>
```